Modern Business Card

Modern professional business card with more than just logo and demographic info. Something memorable.

We are a trendy/modern chiropractic group with an emphasis on neurology, hence the minimalist-type brain logo. We want to convey that modern and technical aspect with professionalism and the elite nature of our practice environment.

```html
<!DOCTYPE html>
<html lang="en">
<head>
<meta charset="utf-8">
<title>Meridian Chiropractic – Business Card</title>
<link rel="stylesheet" href="https://fonts.googleapis.com/css2?family=Quattrocento:wght@400&family=Lustria&family=Saira+Semi+Condensed:wght@600&display=swap">
<style>
  :root {
    --backdrop: #c9c9c9;
    --brand-blue: #3e62a0;
    --card-white: #f3f3f3;
    --ink: #1c1c1c;
    --ink-soft: #3a3a3a;
    --on-blue: #eef0f4;
  }
  * { margin: 0; padding: 0; box-sizing: border-box; }
  html, body {
    width: 1200px; height: 576px; overflow: hidden;
    background: var(--backdrop);
  }
  .canvas { position: relative; width: 1200px; height: 576px; }

  .card {
    position: absolute;
    border-radius: 10px;
    overflow: hidden;
  }

  .wordmark {
    font-family: "Quattrocento", serif;
    font-weight: 400;
    text-transform: uppercase;
    line-height: 1;
  }

  /* Front */
  .card-front {
    left: 82px; top: 139px; width: 485px; height: 293px;
    background: var(--brand-blue);
  }
  .card-front .wordmark {
    position: absolute; left: 0; right: 0; top: 96px;
    color: var(--on-blue); text-align: center;
  }
  .card-front .wordmark-main { display: block; font-size: 66px; letter-spacing: 0.5px; }
  .card-front .wordmark-sub  { display: block; font-size: 33px; margin-top: 2px; letter-spacing: 0.3px; }

  /* Back */
  .card-back {
    left: 602px; top: 138px; width: 481px; height: 291px;
    background: var(--card-white);
  }
  .brand-square {
    position: absolute; left: 0; top: 58px;
    width: 176px; height: 176px;
    background: var(--brand-blue);
  }
  .card-back .wordmark { position: absolute; left: 256px; top: 36px; color: var(--ink); }
  .card-back .wordmark-main { display: block; font-size: 36px; letter-spacing: 0.3px; }
  .card-back .wordmark-sub  { display: block; font-size: 18px; margin-top: -1px; letter-spacing: 0.2px; }

  .person { position: absolute; left: 256px; top: 101px; }
  .person-name {
    font-family: "Saira Semi Condensed", "Arial Narrow", sans-serif;
    font-weight: 600; font-size: 19px; line-height: 24px; color: var(--brand-blue);
  }
  .person-role {
    font-family: "Lustria", serif; font-size: 12px; line-height: 18px; color: var(--ink-soft);
  }

  .contact-list {
    position: absolute; left: 256px; top: 163px;
    list-style: none;
    font-family: "Lustria", serif; font-size: 12px; color: var(--ink-soft);
  }
  .contact-list li { display: flex; align-items: center; height: 18px; }
  .contact-list svg { width: 10px; height: 10px; margin-right: 11px; fill: var(--brand-blue); flex: none; }
  .address {
    position: absolute; left: 256px; top: 222px;
    font-family: "Lustria", serif; font-style: normal;
    font-size: 12px; line-height: 18px; color: var(--ink-soft);
  }
</style>
</head>
<body>
<main class="canvas">

  <section class="card card-front" aria-label="Card front">
    <h1 class="wordmark">
      <span class="wordmark-main">Meridian</span>
      <span class="wordmark-sub">Chiropractic</span>
    </h1>
  </section>

  <section class="card card-back" aria-label="Card back">
    <div class="brand-square"></div>

    <h2 class="wordmark">
      <span class="wordmark-main">Meridian</span>
      <span class="wordmark-sub">Chiropractic</span>
    </h2>

    <div class="person">
      <p class="person-name">Jane Roe Parker</p>
      <p class="person-role">Managing Director</p>
    </div>

    <ul class="contact-list">
      <li>
        <svg viewBox="0 0 10 10" aria-hidden="true"><path d="M1 3.2C1 2 2.6 1 5 1s4 1 4 2.2L7.4 4 6.6 3H3.4L2.6 4zM2.4 9l.8-4.6h3.6L7.6 9z"/></svg>
        555-010-0199
      </li>
      <li>
        <svg viewBox="0 0 10 10" aria-hidden="true"><path d="M0 2h10v.6L5 5.6 0 2.6zM0 3.6l5 3 5-3V8H0z"/></svg>
        jane@meridianchiro.com
      </li>
      <li>
        <svg viewBox="0 0 10 10" aria-hidden="true"><path d="M5 0a5 5 0 1 0 0 10A5 5 0 0 0 5 0zm0 1c.8.7 1.3 2 1.4 3.5H3.6C3.7 3 4.2 1.7 5 1zm-1.4 4.5h2.8C6.3 7 5.8 8.3 5 9c-.8-.7-1.3-2-1.4-3.5zM1 4.5C1.2 3 2 1.9 3 1.3 2.7 2.2 2.6 3.3 2.6 4.5zm0 1h1.6c0 1.2.1 2.3.4 3.2C2 8.1 1.2 7 1 5.5zm6.4 0H9C8.8 7 8 8.1 7 8.7c.3-.9.4-2 .4-3.2zm0-1c0-1.2-.1-2.3-.4-3.2C8 1.9 8.8 3 9 4.5z"/></svg>
        www.meridianchiro.com
      </li>
    </ul>

    <address class="address">
      48 Harbor Lane, Suite 12,<br>
      Lakeview, US 100200
    </address>
  </section>

</main>
</body>
</html>
```